Business Card Design for Marketing Firm

Looking for business card design for higher end marketing firm. Clean but impressionable/trendy. We are a marketing firm that represents manufacturers in the foodservice equipment and supply industry. Our customers are end users such has hotels, restaurants, country clubs, convention centers and casinos as well as distributors of restaurants supplies and equipment, and manufacturers of foodservice equipment and supplies.
Target Market(s)
Hotels, Restaurants, Supply & Equipment Distributors, Foodservice Manufacturers
Industry/Entity Type
Foodservice/Hospitality
Contact Information for Business Card
Name, Title, Contact Number, Email, Website, Social Media, Address
Requirements
Must have
- Clean & Simple but Serious and Impressionable

```html
<!DOCTYPE html>
<html lang="en">
<head>
<meta charset="utf-8">
<title>Harbor Table Reps – Business Card</title>
<link rel="stylesheet" href="https://fonts.googleapis.com/css2?family=Montserrat:wght@700&family=Arimo:wght@400&display=swap">
<style>
  :root {
    --stage: #141416;
    --card-blue: #03027f;
    --card-blue-soft: #0b0a96;
    --ink-white: #ffffff;
    --ink-muted: #e6e6f5;
  }
  * { box-sizing: border-box; margin: 0; padding: 0; }
  html, body { width: 1200px; height: 963px; overflow: hidden; background: var(--stage); }
  .stage { position: relative; width: 1200px; height: 963px; }

  .card {
    position: absolute;
    left: 270px;
    width: 660px;
    height: 377px;
    border-radius: 22px;
    background: var(--card-blue);
    overflow: hidden;
  }
  .card--front { top: 70px; }
  .card--back  { top: 510px; }

  /* Company name, set plainly */
  .brand {
    position: absolute;
    display: flex;
    align-items: center;
    gap: 12px;
    font-family: "Montserrat", sans-serif;
    font-weight: 700;
    font-size: 22px;
    letter-spacing: 0.5px;
    color: var(--ink-white);
    white-space: nowrap;
  }
  .brand__mark { width: 14px; height: 14px; background: var(--ink-white); flex: none; }

  .card--front .brand { left: 150px; top: 62px; }
  .card--back .brand { left: 50%; top: 50%; transform: translate(-50%, -50%); }

  .contact { position: absolute; left: 60px; top: 160px; font-family: "Arimo", sans-serif; color: var(--ink-white); font-size: 15px; line-height: 1.45; }
  .contact__address { margin-left: 34px; margin-bottom: 10px; }
  .contact__row { display: flex; align-items: center; gap: 10px; }
  .contact__row svg { width: 15px; height: 15px; flex: none; }

  .person { position: absolute; right: 50px; top: 150px; text-align: right; }
  .person__name { font-family: "Montserrat", sans-serif; font-weight: 700; font-size: 22px; color: var(--ink-white); letter-spacing: 0.5px; }
  .person__role { font-family: "Arimo", sans-serif; font-size: 16px; color: var(--ink-muted); margin-top: 2px; }

  .edge-tab { position: absolute; right: 0; top: 205px; width: 26px; height: 32px; background: var(--ink-white); border-radius: 3px 0 0 3px; }

  .watermark-area {
    position: absolute; left: 230px; top: 200px; width: 300px; height: 150px;
    background: radial-gradient(ellipse at center, var(--card-blue-soft) 0%, var(--card-blue) 70%);
  }

  .social { position: absolute; right: 120px; bottom: 26px; display: flex; gap: 10px; }
  .social__dot { width: 16px; height: 16px; border: 1.5px solid var(--ink-white); border-radius: 50%; }

  .pattern-area {
    position: absolute; inset: 0;
    background: linear-gradient(135deg, var(--card-blue) 0%, #0a0a8f 45%, var(--card-blue) 100%);
  }
</style>
</head>
<body>
<main class="stage">

  <section class="card card--front" aria-label="Business card front">
    <div class="watermark-area" role="img" aria-label="Large faint brand decoration"></div>

    <p class="brand"><span class="brand__mark"></span>HARBOR TABLE REPS</p>

    <div class="contact">
      <p class="contact__address">Your Address, City<br>State, Zip 0000</p>
      <p class="contact__row">
        <svg viewBox="0 0 16 16" aria-hidden="true"><path d="M4 1.5 6 5 4.5 6.5a8 8 0 0 0 5 5L11 10l3.5 2-1 2.5C7.5 15 1 8.5 1.5 2.5Z" fill="none" stroke="#fff" stroke-width="1.3" stroke-linejoin="round"/></svg>
        555-014-2100
      </p>
      <p class="contact__row">
        <svg viewBox="0 0 16 16" aria-hidden="true"><rect x="1.5" y="3.5" width="13" height="9" rx="1" fill="none" stroke="#fff" stroke-width="1.3"/><path d="M1.5 4 8 9l6.5-5" fill="none" stroke="#fff" stroke-width="1.3"/></svg>
        hello@harbortablereps.com
      </p>
      <p class="contact__row">
        <svg viewBox="0 0 16 16" aria-hidden="true"><circle cx="8" cy="8" r="6.5" fill="none" stroke="#fff" stroke-width="1.3"/><ellipse cx="8" cy="8" rx="3" ry="6.5" fill="none" stroke="#fff" stroke-width="1.1"/><path d="M1.5 8h13M2.5 5h11M2.5 11h11" stroke="#fff" stroke-width="1"/></svg>
        www.harbortablereps.com
      </p>
    </div>

    <div class="person">
      <p class="person__name">DANIEL REYES</p>
      <p class="person__role">Manager</p>
    </div>

    <div class="edge-tab"></div>

    <div class="social" role="img" aria-label="Social media links">
      <span class="social__dot"></span><span class="social__dot"></span>
    </div>
  </section>

  <section class="card card--back" aria-label="Business card back">
    <div class="pattern-area" role="img" aria-label="Repeating embossed brand pattern"></div>
    <p class="brand"><span class="brand__mark"></span>HARBOR TABLE REPS</p>
  </section>

</main>
</body>
</html>
```